Animal Eye Clinic needs a Business card

We are a new veterinary ophthalmology practice (Ridgeline Pet Vision Care) and we need a business card designed. We only see animal eyes - we are not a regular veterinary clinic. We already have a logo. We are looking for a professional, good looking business card to hand out to our clients. We are looking for something simple but professional and contemporary. Our logo is likely the only picture/graphic that needs to be on the card.
Updates

Contact Information for Business Card

Delia Vossman, BSc, DVM, MSc, DipACVO
Veterinary Ophthalmologist

Phone: 250.418.3927
Email: ridgelinepetvisioncare@mailbox-example.net
Website: ridgelinepetvisioncare-example.net
Address: 1874 Thornbury Rd
Kelowna, BC, V1X 4M9

Colors

Designer to choose colors to be used in the design.

Requirements
Must have
• Our logo (attached)

```html
<!DOCTYPE html>
<html lang="en">
<head>
<meta charset="utf-8">
<title>Ridgeline Pet Vision Care – Business Card</title>
<link rel="stylesheet" href="https://fonts.googleapis.com/css2?family=Roboto:wght@400;700&display=swap">
<style>
  :root {
    --bg: #e6e7e8;
    --teal: #0f9aab;
    --teal-deep: #0b8494;
    --grey: #7b7b7b;
    --white: #ffffff;
    --shadow: rgba(0,0,0,0.18);
  }
  * { box-sizing: border-box; margin: 0; padding: 0; }
  html, body { width: 1200px; height: 901px; overflow: hidden; }
  body {
    background: var(--bg);
    font-family: "Roboto", Arial, sans-serif;
    position: relative;
  }
  .card {
    position: absolute;
    top: 296px;
    width: 540px;
    height: 309px;
    box-shadow: 0 8px 22px var(--shadow);
    overflow: hidden;
  }
  /* front */
  .card-front {
    left: 40px;
    background: var(--teal);
    display: flex;
    align-items: center;
    justify-content: center;
    gap: 16px;
  }
  .brand-dot {
    width: 54px; height: 54px;
    border-radius: 50%;
    background: var(--teal-deep);
  }
  .brand-name {
    color: var(--teal-deep);
    font-weight: 700;
    font-size: 25px;
    letter-spacing: 0.5px;
    text-transform: uppercase;
    line-height: 1.15;
  }
  /* back */
  .card-back {
    left: 620px;
    background: var(--grey);
    color: var(--white);
  }
  .brand-panel {
    position: absolute;
    top: 0; right: 0;
    width: 205px; height: 100%;
    background: var(--white);
    display: flex;
    flex-direction: column;
    align-items: center;
    justify-content: center;
    gap: 14px;
    padding: 0 18px;
    text-align: center;
  }
  .brand-panel .brand-dot { width: 70px; height: 70px; background: var(--teal); }
  .brand-panel .brand-name { color: var(--teal); font-size: 17px; }
  .contact {
    position: absolute;
    left: 28px; top: 30px;
    width: 300px;
  }
  .person { font-size: 19px; font-weight: 700; }
  .person .creds { font-size: 12px; font-weight: 400; }
  .role { font-size: 14px; margin-top: 3px; }
  .address { font-size: 13px; line-height: 1.35; margin-top: 42px; }
  .lines { list-style: none; margin-top: 34px; font-size: 12px; line-height: 1.55; }
  .lines li { display: flex; align-items: center; gap: 7px; white-space: nowrap; }
  .lines svg { width: 11px; height: 11px; fill: var(--white); flex: none; }
</style>
</head>
<body>
  <section class="card card-front" aria-label="Card front">
    <span class="brand-dot"></span>
    <span class="brand-name">Ridgeline Pet<br>Vision Care</span>
  </section>

  <section class="card card-back" aria-label="Card back">
    <div class="contact">
      <p class="person">Delia Vossman<span class="creds">, BSc, DVM, MSc, DipACVO</span></p>
      <p class="role">Veterinary Ophthalmologist</p>
      <p class="address">1874 Thornbury Rd<br>Kelowna, BC, V1X 4M9</p>
      <ul class="lines">
        <li><svg viewBox="0 0 24 24"><path d="M6.6 10.8a15.1 15.1 0 0 0 6.6 6.6l2.2-2.2a1 1 0 0 1 1-.25 11.4 11.4 0 0 0 3.6.57 1 1 0 0 1 1 1V20a1 1 0 0 1-1 1A17 17 0 0 1 3 4a1 1 0 0 1 1-1h3.5a1 1 0 0 1 1 1c0 1.25.2 2.45.57 3.57a1 1 0 0 1-.25 1z"/></svg>250.418.3927</li>
        <li><svg viewBox="0 0 24 24"><path d="M2 5h20v14H2z M2 5l10 8 10-8" stroke="#7b7b7b" stroke-width="1.5"/></svg>ridgelinepetvisioncare@mailbox-example.net</li>
        <li><svg viewBox="0 0 24 24"><circle cx="12" cy="12" r="10"/></svg>www.ridgelinepetvisioncare-example.net</li>
      </ul>
    </div>
    <div class="brand-panel">
      <span class="brand-dot"></span>
      <span class="brand-name">Ridgeline Pet Vision Care</span>
    </div>
  </section>
</body>
</html>
```